Label Design for Food Brand

We want a modern label for our spice blends. We are completely open in which direction, it should be modern and beautiful.

Use for Sample spice mixture: "Kelvo Dusk"

Here the Packaging:
https://www.merlitrove-example.com/media/xlarge/1700_1.jpg
Abmessung: Ø 54 x 67 mm

Target Market(s)

Food

Industry/Entity Type

Food

Requirements
Must have
• Logo, Name of Flavr
Should not have
• Images of food

```html
<!DOCTYPE html>
<html lang="en">
<head>
<meta charset="UTF-8">
<title>Kelvo Dusk – Spice Blend Label</title>
<link href="https://fonts.googleapis.com/css2?family=Montserrat:wght@300;400;700;800&display=swap" rel="stylesheet">
<style>
  :root {
    --page: #ffffff;
    --label: #1f1f1f;
    --label-edge: #2b2b2b;
    --ink: #ffffff;
  }
  * { margin: 0; padding: 0; box-sizing: border-box; }
  html, body {
    width: 1200px; height: 750px; overflow: hidden;
    background: var(--page);
    font-family: "Montserrat", sans-serif;
  }
  .label {
    position: absolute; left: 320px; top: 115px;
    width: 560px; height: 520px;
    background: radial-gradient(circle at 45% 45%, var(--label-edge), var(--label) 75%);
    color: var(--ink);
  }
  .brand {
    position: absolute; left: 52px; top: 80px; height: 360px;
    writing-mode: vertical-rl; transform: rotate(180deg);
    font-weight: 700; font-size: 34px; letter-spacing: 2px; line-height: 1;
    text-align: left;
  }
  .brand-rule {
    position: absolute; left: 110px; top: 55px;
    width: 3px; height: 420px; background: var(--ink);
  }
  .product-name {
    position: absolute; left: 140px; top: 95px; line-height: 0.9;
  }
  .product-name .light { display: block; font-weight: 300; font-size: 104px; letter-spacing: 2px; }
  .product-name .bold { display: block; font-weight: 800; font-size: 100px; letter-spacing: 1px; }
  .tagline {
    position: absolute; left: 142px; top: 320px;
    font-size: 23px; line-height: 1.1; letter-spacing: 0.5px;
  }
  .tagline .light { font-weight: 300; }
  .tagline .bold { font-weight: 800; }
  .claims-rule {
    position: absolute; left: 142px; top: 392px;
    width: 390px; height: 3px; background: var(--ink);
  }
  .claims {
    position: absolute; left: 142px; top: 395px; width: 390px;
    display: flex; height: 56px;
  }
  .claim {
    flex: 1; display: flex; align-items: flex-end; justify-content: center;
    font-size: 14px; font-weight: 400; letter-spacing: 0.5px;
    border-left: 3px solid var(--ink); padding-bottom: 4px;
  }
  .claim:first-child { border-left: none; justify-content: flex-start; padding-left: 10px; }
  .claim b { font-weight: 800; margin-left: 4px; }
</style>
</head>
<body>
  <div class="label">
    <div class="brand">HALDENWICK</div>
    <div class="brand-rule"></div>
    <h1 class="product-name">
      <span class="light">KELVO</span>
      <span class="bold">DUSK</span>
    </h1>
    <p class="tagline">
      <span class="light">HANDCRAFTED WITH</span> <span class="bold">HIGHEST</span><br>
      <span class="bold">QUALITY INGREDIENTS</span>
    </p>
    <div class="claims-rule"></div>
    <div class="claims">
      <div class="claim">GLUTEN <b>FREE</b></div>
      <div class="claim">NO <b>MSG</b></div>
      <div class="claim">NO <b>SOY</b></div>
    </div>
  </div>
</body>
</html>
```